Keystone Polished Concrete & Grinding
I'm looking for a business card and logo design for my
new Polished Concrete & Grinding business,
If you were to look up Keystone in the dictionary it would
say, first in importance, order, or position; leading.
Polished Concrete floors are a niche market, that are being used currently in Shopping centres, office spaces and by most high end architects, builders and designers.
i need my business card & logo to stand out from my
competitors, i need my design + logo to reflect this it
needs to be simple, professional, eye catching, easy
to read and scream quality. The logo will need to be
suitable for a whole range of applications including,
uniforms, letter heads, stickers, and eventually
incorporating in vehicle vinyl wrapping.
Target Market(s)
Builders, architects, Interior designers & home owners
Contact Information for Business Card
Front side:
- Keystone Polished Concrete & Grinding.
- Logo
Rear side:
- Liam Varesko
- 0438175092
- info@keystonepcg-example.com.au
- commercial - domestic - industrial
- (later down the line website & space for
social media links
www.keystonepolishedslab-example.com.au)
Colors
Designer to choose colors to be used in the design.
Look and feel
Each slider illustrates characteristics of the customer's brand and the style your logo design should communicate.

```html
<!DOCTYPE html>
<html lang="en">
<head>
<meta charset="utf-8">
<title>Keystone Polished Concrete &amp; Grinding – Business Card</title>
<link rel="stylesheet" href="https://fonts.googleapis.com/css2?family=Roboto:wght@400;500&display=swap">
<style>
  :root {
    --backdrop: #a4a4a4;
    --card-dark: #1f1f1f;
    --card-light: #ffffff;
    --brand-blue: #1ea5df;
    --ink: #1c1c1c;
    --on-dark: #ffffff;
  }
  * { margin: 0; padding: 0; box-sizing: border-box; }
  html, body {
    width: 1200px;
    height: 930px;
    overflow: hidden;
  }
  body {
    background: var(--backdrop);
    font-family: "Roboto", Arial, sans-serif;
    position: relative;
  }
  .card {
    position: absolute;
    width: 520px;
    height: 300px;
    border-radius: 22px;
    box-shadow: 0 10px 24px rgba(0, 0, 0, 0.28);
  }
  .card--front {
    left: 80px;
    top: 120px;
    background: var(--card-dark);
  }
  .card--back {
    left: 600px;
    top: 510px;
    background: var(--card-light);
  }

  /* Company name set as plain text in one colour and weight */
  .company {
    position: absolute;
    color: var(--brand-blue);
    font-weight: 500;
    white-space: nowrap;
    line-height: 1.2;
  }
  .card--front .company {
    left: 0;
    right: 0;
    top: 120px;
    text-align: center;
    font-size: 22px;
  }
  .card--back .company {
    right: 30px;
    top: 44px;
    font-size: 16px;
  }

  .services {
    position: absolute;
    left: 0;
    right: 0;
    bottom: 40px;
    text-align: center;
    color: var(--on-dark);
    font-size: 15px;
    letter-spacing: 0.5px;
  }

  .holder {
    position: absolute;
    left: 30px;
    top: 140px;
  }
  .holder__name {
    color: var(--brand-blue);
    font-size: 30px;
    font-weight: 400;
    letter-spacing: 2px;
    text-transform: uppercase;
    line-height: 1;
  }
  .holder__role {
    margin-top: 6px;
    font-size: 13px;
    color: var(--ink);
  }
  .rule {
    position: absolute;
    left: 130px;
    right: 30px;
    top: 192px;
    height: 1px;
    background: var(--brand-blue);
  }
  .contacts {
    position: absolute;
    left: 30px;
    top: 212px;
    list-style: none;
  }
  .contacts__item {
    display: flex;
    align-items: center;
    gap: 8px;
    font-size: 14px;
    color: var(--ink);
    line-height: 24px;
  }
  .contacts__icon {
    width: 12px;
    height: 12px;
    flex: none;
  }
</style>
</head>
<body>

  <section class="card card--front" aria-label="Business card front">
    <p class="company">Keystone Polished Concrete &amp; Grinding</p>
    <p class="services">COMMERCIAL - DOMESTIC - INDUSTRIAL</p>
  </section>

  <section class="card card--back" aria-label="Business card back">
    <p class="company">Keystone Polished Concrete &amp; Grinding</p>

    <div class="holder">
      <h1 class="holder__name">Liam Varesko</h1>
      <p class="holder__role">Director</p>
    </div>
    <div class="rule"></div>

    <ul class="contacts">
      <li class="contacts__item">
        <svg class="contacts__icon" viewBox="0 0 12 12" aria-hidden="true">
          <path d="M2.5 1 L4.5 1 L5 3.5 L3.8 4.4 Q4.8 6.9 7.6 8.2 L8.5 7 L11 7.5 L11 9.5 Q11 11 9.5 11 Q1 10 1 2.5 Q1 1 2.5 1 Z" fill="var(--brand-blue)"/>
        </svg>
        0438175092
      </li>
      <li class="contacts__item">
        <svg class="contacts__icon" viewBox="0 0 12 12" aria-hidden="true">
          <rect x="1" y="2.5" width="10" height="7" fill="none" stroke="var(--brand-blue)" stroke-width="1.2"/>
          <path d="M1 2.5 L6 6.5 L11 2.5" fill="none" stroke="var(--brand-blue)" stroke-width="1.2"/>
        </svg>
        info@keystonepcg-example.com.au
      </li>
      <li class="contacts__item">
        <svg class="contacts__icon" viewBox="0 0 12 12" aria-hidden="true">
          <circle cx="6" cy="6" r="5" fill="none" stroke="var(--brand-blue)" stroke-width="1.2"/>
          <ellipse cx="6" cy="6" rx="2.2" ry="5" fill="none" stroke="var(--brand-blue)" stroke-width="1"/>
          <path d="M1 6 H11" stroke="var(--brand-blue)" stroke-width="1"/>
        </svg>
        www.keystonepolishedslab-example.com.au
      </li>
    </ul>
  </section>

</body>
</html>
```